TalkHarbor - Language Coaching Services

Sleek, innovative, trendy design for Language Coaching business.

TalkHarbor is a new UK based company that provides Language Coaching services. We offer highly personalized on-line and face to face language courses. We also impart learning techniques workshops based on the latest neuroscience research for second-language acquisition.

Target Market(s)

See attached info

Industry/Entity Type

Consulting

Contact Information for Business Card

TalkHarbor
DaniaKV@talkharbor.co.uk
TalkHarbor.co.uk
London, UK

Font styles to use
Sans Serif

```html
<!DOCTYPE html>
<html lang="en">
<head>
<meta charset="utf-8">
<title>TalkHarbor Business Cards</title>
<link rel="stylesheet" href="https://fonts.googleapis.com/css2?family=Roboto:wght@400;500;700&family=Roboto+Condensed:wght@400;700&display=swap">
<style>
  :root {
    --bg: #2a2a2c;
    --blue-deep: #0a5f95;
    --blue-mid: #0f86c4;
    --blue-bright: #28b8ee;
    --white: #ffffff;
    --white-soft: rgba(255,255,255,0.88);
    --logo-blue: #1178b5;
  }
  * { margin: 0; padding: 0; box-sizing: border-box; }
  html, body { width: 1200px; height: 896px; overflow: hidden; }
  body {
    background: var(--bg);
    font-family: "Roboto", Arial, sans-serif;
    color: var(--white);
    display: flex;
    align-items: center;
    justify-content: center;
    gap: 40px;
  }
  .card {
    position: relative;
    width: 540px;
    height: 310px;
    border-radius: 22px;
    overflow: hidden;
    background: linear-gradient(200deg, var(--blue-deep) 0%, var(--blue-mid) 55%, var(--blue-bright) 100%);
    box-shadow: 0 14px 30px rgba(0,0,0,0.45);
  }

  /* Back: services */
  .card-back { text-align: center; padding: 34px 36px 0; }
  .brand {
    display: flex; align-items: center; justify-content: center; gap: 14px;
  }
  .brand-dot {
    width: 50px; height: 50px; border-radius: 50%;
    border: 4px solid var(--white);
  }
  .brand-name {
    font-family: "Roboto", Arial, sans-serif;
    font-weight: 500; font-size: 40px; letter-spacing: 1px; color: var(--white);
  }
  .services-title {
    margin-top: 20px; font-weight: 700; font-size: 21px;
  }
  .services-rule { height: 1px; background: var(--white-soft); margin: 10px 0; }
  .services-intro { font-family: "Roboto Condensed", Arial, sans-serif; font-size: 14px; }
  .services-list {
    font-family: "Roboto Condensed", Arial, sans-serif;
    font-size: 13.5px; line-height: 1.55; color: var(--white-soft);
  }

  /* Front: contact */
  .card-front .disc {
    position: absolute; left: 255px; top: -65px;
    width: 350px; height: 350px; border-radius: 50%;
    background: var(--white);
  }
  .card-front .band {
    position: absolute; left: 150px; top: -40px; width: 90px; height: 420px;
    background: rgba(255,255,255,0.12); transform: rotate(28deg);
  }
  .front-brand {
    position: absolute; left: 300px; top: 85px; width: 260px;
    display: flex; align-items: center; gap: 10px;
  }
  .front-brand .brand-dot { width: 34px; height: 34px; border-color: var(--logo-blue); border-width: 4px; }
  .front-brand .brand-name { font-size: 30px; color: var(--logo-blue); }
  .address {
    position: absolute; left: 30px; top: 30px;
    font-size: 14px; line-height: 1.45; letter-spacing: 0.5px; color: var(--white-soft);
  }
  .person { position: absolute; left: 30px; top: 130px; }
  .person-name { font-weight: 700; font-size: 24px; letter-spacing: 1px; }
  .person-role { font-size: 13px; margin-top: 2px; color: var(--white-soft); }
  .contacts {
    position: absolute; left: 30px; top: 210px; list-style: none;
    font-size: 14px; line-height: 1.65; letter-spacing: 0.4px;
  }
  .contacts li { display: flex; align-items: center; gap: 8px; }
  .contacts svg { width: 12px; height: 12px; fill: var(--white); }
</style>
</head>
<body>
  <section class="card card-back">
    <div class="brand">
      <span class="brand-dot"></span>
      <span class="brand-name">TalkHarbor</span>
    </div>
    <h2 class="services-title">Our Services</h2>
    <div class="services-rule"></div>
    <p class="services-intro">We offer highly customized coaching sessions and self-study content.</p>
    <div class="services-rule"></div>
    <p class="services-list">
      Face to face language coaching sessions | On-line language coaching sessions<br>
      Personalized Newsletters for self-learners | Language Learning Techniques Workshops<br>
      Mindful Learning Workshops | Access to premium content, resources.
    </p>
  </section>

  <section class="card card-front">
    <div class="band"></div>
    <div class="disc"></div>
    <div class="front-brand">
      <span class="brand-dot"></span>
      <span class="brand-name">TalkHarbor</span>
    </div>
    <p class="address">27 Harbour Lane,<br>London, UK, E14 5AB</p>
    <div class="person">
      <p class="person-name">DANIA KOVAC</p>
      <p class="person-role">Director</p>
    </div>
    <ul class="contacts">
      <li><svg viewBox="0 0 12 12"><path d="M2.5 1 4.5 1 5.3 3.6 4 4.6a7 7 0 0 0 3.4 3.4l1-1.3 2.6.8v2C11 10.3 10.3 11 9.5 11 5 11 1 7 1 2.5 1 1.7 1.7 1 2.5 1Z"/></svg>(555) 014-2270</li>
      <li><svg viewBox="0 0 12 12"><path d="M1 2.5h10v7H1z M1.5 3 6 6.5 10.5 3" fill="none" stroke="#fff" stroke-width="1.2"/></svg>DaniaKV@talkharbor.co.uk</li>
      <li><svg viewBox="0 0 12 12"><circle cx="6" cy="6" r="5" fill="none" stroke="#fff" stroke-width="1.2"/><path d="M1 6h10M6 1c-2.2 2.8-2.2 7.2 0 10M6 1c2.2 2.8 2.2 7.2 0 10" fill="none" stroke="#fff" stroke-width="1"/></svg>www.talkharbor.co.uk</li>
    </ul>
  </section>
</body>
</html>
```